Business Card Design

Velora Pixel Outreach

An online marketing consulting & strategy business for the cosmetic niche

We specialise in Increasing Leads, Conversions & Content Marketing

I am looking for a very clean, BOLD business card that is simple & effective

Target Market(s)

cosmetic surgeons & cosmetic clinics

Industry/Entity Type

Marketing

Contact Information for Business Card

Dermot Kalway
Online Marketing Strategist

Dermot@VeloraPixelOutreach.example
0492 158 620

LinkedIn: in/dermotkalway

```html
<!DOCTYPE html>
<html lang="en">
<head>
<meta charset="utf-8">
<title>Velora Pixel Outreach – Business Card</title>
<link rel="stylesheet" href="https://fonts.googleapis.com/css2?family=Open+Sans:wght@400;600&display=swap">
<style>
  :root {
    --backdrop: #a9a8a8;
    --card: #ffffff;
    --blue: #2aa9e0;
    --green: #9bc93a;
    --ink: #6b6b6d;
    --text: #4d4d4f;
    --shadow: rgba(0,0,0,0.45);
  }
  * { box-sizing: border-box; margin: 0; padding: 0; }
  html, body { width: 1200px; height: 900px; overflow: hidden; }
  body {
    background: var(--backdrop);
    position: relative;
    font-family: "Open Sans", Arial, sans-serif;
  }
  .card {
    position: absolute;
    width: 566px;
    background: var(--card);
    box-shadow: 3px 4px 5px var(--shadow);
    overflow: hidden;
  }
  .card--square { height: 342px; }
  .card--rounded { height: 330px; border-radius: 28px; }
  .pos-front-a { left: 18px; top: 108px; }
  .pos-back-a { left: 612px; top: 108px; }
  .pos-front-b { left: 18px; top: 485px; }
  .pos-back-b { left: 612px; top: 483px; }

  /* Front */
  .front-mark {
    position: absolute;
    left: 209px; top: 64px;
    width: 144px; height: 128px;
    border: 3px solid var(--blue);
  }
  .card--rounded .front-mark { top: 60px; }
  .front-name {
    position: absolute;
    left: 0; right: 0; top: 204px;
    text-align: center;
    color: var(--ink);
    font-weight: 600;
    font-size: 22px;
    line-height: 25px;
    letter-spacing: 4px;
    text-transform: uppercase;
  }
  .card--rounded .front-name { top: 196px; }
  .front-band {
    position: absolute;
    left: 0; top: 282px;
    width: 566px; height: 34px;
  }
  .card--rounded .front-band { top: 271px; }

  /* Back */
  .back-strip {
    position: absolute;
    left: 0; top: 0; bottom: 0;
    width: 113px;
    background: linear-gradient(to bottom, var(--blue) 0%, var(--green) 100%);
  }
  .back-rule {
    position: absolute;
    left: 121px; top: 0; bottom: 0;
    width: 2px;
    background: var(--blue);
  }
  .back-mark {
    position: absolute;
    left: 48px; top: 40px;
    width: 92px; height: 92px;
    background: var(--card);
  }
  .back-company {
    position: absolute;
    left: 150px; top: 46px;
    color: var(--ink);
    font-weight: 600;
    font-size: 27px;
    line-height: 28px;
    letter-spacing: 3px;
    text-transform: uppercase;
  }
  .holder {
    position: absolute;
    left: 128px; top: 144px;
    font-size: 20px;
    font-weight: 400;
    padding-bottom: 2px;
    border-bottom: 1px solid var(--green);
    width: 116px;
    white-space: nowrap;
  }
  .holder .first { color: var(--blue); }
  .holder .last { color: var(--green); }
  .holder-role {
    position: absolute;
    left: 128px; top: 176px;
    font-size: 14px;
    font-weight: 600;
    color: var(--green);
  }
  .contact-list {
    position: absolute;
    left: 143px; top: 219px;
    list-style: none;
  }
  .card--rounded .contact-list { top: 211px; }
  .contact-item {
    display: flex;
    align-items: center;
    height: 32px;
    font-size: 13px;
    color: var(--text);
  }
  .contact-icon {
    width: 18px; height: 18px;
    margin-right: 10px;
    flex: none;
  }
</style>
</head>
<body>

  <!-- Square cut -->
  <section class="card card--square pos-front-a" aria-label="Card front">
    <div class="front-mark"></div>
    <p class="front-name">Velora<br>Pixel<br>Outreach</p>
    <svg class="front-band" viewBox="0 0 566 34" aria-hidden="true">
      <rect width="566" height="34" fill="var(--blue)"/>
      <polygon points="38,34 52,0 60,0 46,34" fill="#fff"/>
      <polygon points="46,34 60,0 80,0 66,34" fill="var(--green)"/>
      <polygon points="66,34 80,0 88,0 74,34" fill="#fff"/>
    </svg>
  </section>

  <section class="card card--square pos-back-a" aria-label="Card back">
    <div class="back-strip"></div>
    <div class="back-rule"></div>
    <div class="back-mark"></div>
    <p class="back-company">Velora<br>Pixel<br>Outreach</p>
    <h2 class="holder"><span class="first">Dermot</span> <span class="last">Kalway</span></h2>
    <p class="holder-role">Online Marketing Strategist</p>
    <ul class="contact-list">
      <li class="contact-item">
        <svg class="contact-icon" viewBox="0 0 18 18" aria-hidden="true"><rect width="18" height="18" rx="2" fill="var(--blue)"/><circle cx="9" cy="9" r="6" fill="none" stroke="#fff" stroke-width="1.2"/><ellipse cx="9" cy="9" rx="2.6" ry="6" fill="none" stroke="#fff" stroke-width="1"/><path d="M3 9h12" stroke="#fff" stroke-width="1"/></svg>
        0492 158 620
      </li>
      <li class="contact-item">
        <svg class="contact-icon" viewBox="0 0 18 18" aria-hidden="true"><rect width="18" height="18" rx="2" fill="var(--blue)"/><rect x="3" y="5" width="12" height="8" fill="none" stroke="#fff" stroke-width="1.2"/><path d="M3 5l6 5 6-5" fill="none" stroke="#fff" stroke-width="1.2"/></svg>
        Dermot@VeloraPixelOutreach.example
      </li>
      <li class="contact-item">
        <svg class="contact-icon" viewBox="0 0 18 18" aria-hidden="true"><rect width="18" height="18" rx="2" fill="var(--blue)"/></svg>
        in/dermotkalway
      </li>
    </ul>
  </section>

  <!-- Rounded cut -->
  <section class="card card--rounded pos-front-b" aria-label="Card front, rounded corners">
    <div class="front-mark"></div>
    <p class="front-name">Velora<br>Pixel<br>Outreach</p>
    <svg class="front-band" viewBox="0 0 566 34" aria-hidden="true">
      <rect width="566" height="34" fill="var(--blue)"/>
      <polygon points="38,34 52,0 60,0 46,34" fill="#fff"/>
      <polygon points="46,34 60,0 80,0 66,34" fill="var(--green)"/>
      <polygon points="66,34 80,0 88,0 74,34" fill="#fff"/>
    </svg>
  </section>

  <section class="card card--rounded pos-back-b" aria-label="Card back, rounded corners">
    <div class="back-strip"></div>
    <div class="back-rule"></div>
    <div class="back-mark"></div>
    <p class="back-company">Velora<br>Pixel<br>Outreach</p>
    <h2 class="holder"><span class="first">Dermot</span> <span class="last">Kalway</span></h2>
    <p class="holder-role">Online Marketing Strategist</p>
    <ul class="contact-list">
      <li class="contact-item">
        <svg class="contact-icon" viewBox="0 0 18 18" aria-hidden="true"><rect width="18" height="18" rx="2" fill="var(--blue)"/><circle cx="9" cy="9" r="6" fill="none" stroke="#fff" stroke-width="1.2"/><ellipse cx="9" cy="9" rx="2.6" ry="6" fill="none" stroke="#fff" stroke-width="1"/><path d="M3 9h12" stroke="#fff" stroke-width="1"/></svg>
        0492 158 620
      </li>
      <li class="contact-item">
        <svg class="contact-icon" viewBox="0 0 18 18" aria-hidden="true"><rect width="18" height="18" rx="2" fill="var(--blue)"/><rect x="3" y="5" width="12" height="8" fill="none" stroke="#fff" stroke-width="1.2"/><path d="M3 5l6 5 6-5" fill="none" stroke="#fff" stroke-width="1.2"/></svg>
        Dermot@VeloraPixelOutreach.example
      </li>
      <li class="contact-item">
        <svg class="contact-icon" viewBox="0 0 18 18" aria-hidden="true"><rect width="18" height="18" rx="2" fill="var(--blue)"/></svg>
        in/dermotkalway
      </li>
    </ul>
  </section>

</body>
</html>
```